Tessmar Fahrwerkstatt
Sehr angenehme zusammenarbeit nicht aufdringlich und genau auf die Wünsche eingegangen. Wir werde sicher noch mehr zusammen Arbeiten. Gruss Lukas Hegemann Inhaber Tessmar Fahrwerkstatt
Zielgruppe
Dinks und Kunden mit viel Erfolg und hohem Ausgabepotential.
Aufgabenstellung
Unsere Firma vertreibt Fahrzeuge im Luxusbereich hauptgebiet Valmerra aber auch andere Sportwagen. Was uns fehlt ist ein optischer Wiedererkennugswert. Deshalb hätten wir gerne ein Visitenkarten Design und Briefpapier Design. Später soll auch noch eine Webseite mit gleichem Wiedererkennungswert entstehen. " Roter Faden "

```html
<!DOCTYPE html>
<html lang="de">
<head>
<meta charset="utf-8">
<title>Tessmar Fahrwerkstatt – Visitenkarte</title>
<link rel="stylesheet" href="https://fonts.googleapis.com/css2?family=Sorts+Mill+Goudy&display=swap">
<style>
  :root {
    --page-bg: #eceef1;
    --card-blue: #2e63a6;
    --card-blue-light: #4378bd;
    --card-blue-dark: #1f4c88;
    --gold: #e3c57c;
    --caption-ink: #222222;
  }
  * { box-sizing: border-box; margin: 0; padding: 0; }
  html, body { width: 1200px; height: 960px; overflow: hidden; }
  body {
    background: var(--page-bg);
    font-family: "Sorts Mill Goudy", Georgia, serif;
    position: relative;
  }
  .spec-caption {
    position: absolute;
    top: 80px; left: 0; width: 1200px;
    text-align: center;
    color: var(--caption-ink);
    font-size: 27px;
    line-height: 1.4;
  }
  .card {
    position: absolute;
    top: 330px;
    width: 520px; height: 336px;
    border-radius: 4px;
    background: linear-gradient(160deg, var(--card-blue-light) 0%, var(--card-blue) 45%, var(--card-blue-dark) 100%);
    box-shadow: 0 14px 30px rgba(0,0,0,0.28);
    color: var(--gold);
  }
  .card--front { left: 60px; }
  .card--back { left: 620px; }
  .card__frame {
    position: absolute;
    inset: 20px;
    border: 1.5px solid var(--gold);
    border-radius: 14px;
  }
  .brand {
    position: absolute;
    left: 0; right: 0;
    display: flex; align-items: center; justify-content: center;
    gap: 12px;
    color: var(--gold);
    white-space: nowrap;
  }
  .brand__dot {
    width: 14px; height: 14px; border-radius: 50%;
    background: var(--gold);
  }
  .card--front .brand { top: 110px; font-size: 30px; }
  .card--back .brand { top: 62px; font-size: 24px; }
  .holder-name {
    position: absolute;
    left: 0; right: 0; top: 232px;
    text-align: center;
    font-size: 26px;
    letter-spacing: 0.5px;
  }
  .contact {
    position: absolute;
    left: 0; right: 0;
    text-align: center;
    font-size: 15px;
    line-height: 1.4;
    white-space: nowrap;
  }
  .contact--web { top: 128px; }
  .contact--details { top: 188px; }
</style>
</head>
<body>
  <p class="spec-caption">
    85mm x 55mm<br>
    Logo und Rahmen mit partiellem:<br>
    Hochglanz-Dispersionslack, Chrom- oder Perlmutt-Effekt
  </p>

  <section class="card card--front" aria-label="Visitenkarte Vorderseite">
    <div class="card__frame"></div>
    <div class="brand"><span class="brand__dot"></span>Tessmar Fahrwerkstatt</div>
    <p class="holder-name">Lukas Hegemann</p>
  </section>

  <section class="card card--back" aria-label="Visitenkarte Rückseite">
    <div class="card__frame"></div>
    <div class="brand"><span class="brand__dot"></span>Tessmar Fahrwerkstatt</div>
    <p class="contact contact--web">www.tessmar-fahrwerk.ch</p>
    <p class="contact contact--details">
      +41790001234<br>
      info@tessmar-fahrwerk.ch<br>
      Büro : Lindenweg 12 - CH 9321 Bergwil<br>
      Showroom : Mühlegasse 4 - CH 6957 Talberg
    </p>
  </section>
</body>
</html>
```